FinTech company looking to revamp and expand client-facing interface for our financial models

Pellworth Engines currently has a very simple website that allows clients to interact with our financial models. We are looking to completely redesign the current site and add several extra pages to provide extra functionality. We want the design to have a modern, slick feel, that will work on both a desktop or a tablet. It should be straightforward for clients to move between different pages at any time, and clear from the layout how to interact with the more advanced features. We have included screenshots of existing pages in the attached design brief, as well as sketches of the functionality required by the new pages, but can't provide a direct link to the current site.
Target Market(s)
Professional investors that will be paying to access the interface
Industry/Entity Type
Finance
Number of Pages Required
4 page
Colors
Designer to choose colors to be used in the design.
Look and feel
Each slider illustrates characteristics of the customer's brand and the style your logo design should communicate.

```html
<!DOCTYPE html>
<html lang="en">
<head>
<meta charset="utf-8">
<title>Pellworth Engines – Factor Selection</title>
<link href="https://fonts.googleapis.com/css2?family=Open+Sans:wght@400;600;700&family=Montserrat:wght@500;600&display=swap" rel="stylesheet">
<style>
  :root{
    --ink:#1a1a1a;
    --teal:#006864;
    --navy:#0c3566;
    --page:#f4f4f4;
    --white:#ffffff;
    --row-alt:#f0f0f0;
    --label:#9a9a9a;
    --line:#e6e6e6;
    --blue:#3d6fb0;
    --olive:#b6b83b;
    --green:#3c9a3c;
  }
  *{box-sizing:border-box;margin:0;padding:0}
  html,body{width:1135px;height:1200px;overflow:hidden}
  body{background:linear-gradient(#e6e6e6 0,#f6f6f6 300px,#f7f7f7 100%);font-family:"Open Sans",sans-serif;color:var(--ink);position:relative}
  .topbar{position:absolute;left:0;top:0;width:1135px;height:52px;background:var(--white);box-shadow:0 2px 8px rgba(0,0,0,.12);display:flex;align-items:stretch}
  .brand{position:absolute;left:63px;top:0;line-height:52px;font-weight:700;font-size:17px;letter-spacing:.2px}
  .tab{position:absolute;top:0;height:52px;line-height:52px;text-align:center;font-weight:700;font-size:13px;border-right:1px solid var(--line)}
  .tab.active{background:var(--navy);color:var(--white);border:none}
  .menu{position:absolute;top:0;height:52px;display:flex;align-items:center;justify-content:center;gap:6px;font-weight:700;font-size:11.5px;border-left:1px solid var(--line);border-right:1px solid var(--line)}
  .menu svg{width:20px;height:20px}
  .pill{position:absolute;left:61px;width:284px;height:35px;background:var(--label);color:var(--white);border-radius:4px;font-family:"Montserrat",sans-serif;font-weight:600;font-size:14.5px;display:flex;align-items:center;justify-content:center}
  .card{position:absolute;left:61px;width:1013px;background:var(--white);box-shadow:0 2px 6px rgba(0,0,0,.12);border-radius:4px;overflow:hidden}
  table{border-collapse:collapse;width:100%;font-size:15px}
  th{height:61px;color:var(--white);font-weight:600;font-size:15px;background:var(--teal);border-left:1px solid rgba(255,255,255,.12)}
  th.id{background:var(--ink);width:384px}
  td{height:59.5px;text-align:center;border-left:1px solid var(--line)}
  tbody tr:nth-child(even) td{background:var(--row-alt)}
  .grid td{height:61px;width:20%}
  .grid tr:nth-child(odd) td{background:var(--row-alt)}
  .grid tr:nth-child(even) td{background:var(--white)}
  .collapse{position:absolute;left:1047px;top:427px;width:28px;height:28px;border-radius:50%;background:#4a4a4a;border:2px solid #ccc;display:flex;align-items:center;justify-content:center}
  .chart-head{height:74px;background:#efefef;position:relative}
  .ctab{position:absolute;top:43px;height:31px;background:var(--white);font-family:"Montserrat",sans-serif;font-weight:600;font-size:14.5px;display:flex;align-items:center;justify-content:center;border-radius:3px 3px 0 0}
  .ctab.current{background:var(--teal);color:var(--white)}
  .ctab.hover{background:#d6d6d6;color:#666;top:35px;height:39px}
  .plot{display:block}
</style>
</head>
<body>
<header class="topbar">
  <div class="brand">PELLWORTH</div>
  <div class="tab active" style="left:170px;width:79px">250D</div>
  <div class="tab" style="left:249px;width:78px">83D</div>
  <div class="tab" style="left:327px;width:79px">42D</div>
  <div class="menu" style="left:524px;width:123px">
    <svg viewBox="0 0 20 20"><path d="M2 10 10 3l8 7M5 8v9h4v-5h2v5h4V8" fill="none" stroke="#1a1a1a" stroke-width="2"/></svg>MODELS</div>
  <div class="menu" style="left:647px;width:154px;border-left:none">
    <svg viewBox="0 0 20 20"><g fill="#1a1a1a"><circle cx="10" cy="10" r="2.4"/><circle cx="10" cy="3" r="1.4"/><circle cx="10" cy="17" r="1.4"/><circle cx="3" cy="10" r="1.4"/><circle cx="17" cy="10" r="1.4"/><circle cx="5" cy="5" r="1.4"/><circle cx="15" cy="5" r="1.4"/><circle cx="5" cy="15" r="1.4"/><circle cx="15" cy="15" r="1.4"/></g></svg>SENSITIVITIES</div>
  <div class="menu" style="left:801px;width:140px;border-left:none">
    <svg viewBox="0 0 20 20"><g fill="none" stroke="#1a1a1a" stroke-width="1.6"><circle cx="5.5" cy="5.5" r="3.5"/><circle cx="14.5" cy="5.5" r="3.5"/><circle cx="5.5" cy="14.5" r="3.5"/><circle cx="14.5" cy="14.5" r="3.5"/></g></svg>PORTFOLIO</div>
  <div class="menu" style="left:941px;width:133px;border-left:none">
    <svg viewBox="0 0 20 20"><rect x="1.5" y="3" width="17" height="14" fill="none" stroke="#1a1a1a" stroke-width="1.6"/><path d="M4 14l4-5 3 3 5-6" fill="none" stroke="#1a1a1a" stroke-width="1.6"/></svg>BACKTEST</div>
</header>

<div class="pill" style="top:87px">Number of Selected Factors : 3</div>
<section class="card" style="top:135px">
  <table>
    <thead><tr><th class="id">ID &#8964;</th><th>Stat 1</th><th>Stat 2</th><th>Stat 3</th><th>Stat 4</th></tr></thead>
    <tbody>
      <tr><td style="border-left:none">Factor 1</td><td>-1.4</td><td>0.094</td><td>6.1</td><td>100</td></tr>
      <tr><td style="border-left:none">Factor 2</td><td>2.8</td><td>0.085</td><td>3.1</td><td>0.7</td></tr>
      <tr><td style="border-left:none">Factor 3</td><td>-3.7</td><td>2.7</td><td>-7.2</td><td>100</td></tr>
    </tbody>
  </table>
</section>

<div class="pill" style="top:423px">Unselected Factors</div>
<div class="collapse"><svg width="14" height="10" viewBox="0 0 14 10"><path d="M2 8l5-5 5 5" fill="none" stroke="#fff" stroke-width="2.2"/></svg></div>
<section class="card" style="top:471px">
  <table class="grid">
    <tr><td style="border-left:none">Factor</td><td>Factor</td><td>Factor</td><td>Factor</td><td>Factor</td></tr>
    <tr><td style="border-left:none">Factor</td><td>Factor</td><td>Factor</td><td>Factor</td><td>Factor</td></tr>
    <tr><td style="border-left:none">Factor</td><td>Factor</td><td>Factor</td><td>Factor</td><td>Factor</td></tr>
    <tr><td style="border-left:none">Factor</td><td>Factor</td><td>Factor</td><td>Factor</td><td>Factor</td></tr>
  </table>
</section>

<section class="card" style="top:760px;height:371px">
  <div class="chart-head">
    <div class="ctab current" style="left:48px;width:135px">Chart</div>
    <div class="ctab" style="left:188px;width:78px">#1</div>
    <div class="ctab" style="left:271px;width:78px">#2</div>
    <div class="ctab" style="left:354px;width:78px">#3</div>
    <div class="ctab hover" style="left:437px;width:78px">#4</div>
  </div>
  <svg class="plot" width="1013" height="297" viewBox="70 955 1160 340" font-family="Open Sans, sans-serif" font-size="11" fill="#555">
    <g stroke="#ececec">
      <line x1="182" y1="1002" x2="182" y2="1205"/><line x1="324" y1="1002" x2="324" y2="1205"/>
      <line x1="465" y1="1002" x2="465" y2="1205"/><line x1="605" y1="1002" x2="605" y2="1205"/>
      <line x1="742" y1="1002" x2="742" y2="1205"/><line x1="882" y1="1002" x2="882" y2="1205"/>
      <line x1="1023" y1="1002" x2="1023" y2="1205"/>
    </g>
    <line x1="155" y1="1205" x2="1077" y2="1205" stroke="#888"/>
    <g text-anchor="end"><text x="151" y="1022">100</text><text x="151" y="1059">80</text><text x="151" y="1096">60</text><text x="151" y="1134">40</text><text x="151" y="1171">20</text><text x="151" y="1209">0</text></g>
    <g text-anchor="middle"><text x="182" y="1230">Jul 2018</text><text x="324" y="1230">Sep 2018</text><text x="465" y="1230">Nov 2018</text><text x="605" y="1230">Jan 2019</text><text x="742" y="1230">Mar 2019</text><text x="882" y="1230">May 2019</text><text x="1023" y="1230">Jul 2019</text></g>
    <g stroke-linecap="round" stroke-width="7" stroke-dasharray="0 7">
      <line x1="202" y1="1018" x2="290" y2="1018" stroke="var(--olive)"/>
      <line x1="740" y1="1021" x2="1000" y2="1021" stroke="var(--olive)"/>
      <line x1="590" y1="1018" x2="1028" y2="1018" stroke="var(--blue)"/>
      <line x1="998" y1="1202" x2="1012" y2="1202" stroke="var(--green)"/>
    </g>
    <g fill="var(--olive)">
      <circle cx="290" cy="1028" r="3.5"/><circle cx="300" cy="1022" r="3.5"/><circle cx="310" cy="1024" r="3.5"/><circle cx="322" cy="1026" r="3.5"/><circle cx="334" cy="1030" r="3.5"/>
      <circle cx="337" cy="1084" r="3.5"/><circle cx="340" cy="1114" r="3.5"/><circle cx="348" cy="1118" r="3.5"/><circle cx="352" cy="1098" r="3.5"/><circle cx="356" cy="1134" r="3.5"/><circle cx="362" cy="1122" r="3.5"/><circle cx="368" cy="1110" r="3.5"/><circle cx="374" cy="1118" r="3.5"/><circle cx="380" cy="1078" r="3.5"/><circle cx="386" cy="1060" r="3.5"/><circle cx="394" cy="1048" r="3.5"/><circle cx="402" cy="1020" r="3.5"/><circle cx="408" cy="1024" r="3.5"/>
      <circle cx="412" cy="1082" r="3.5"/><circle cx="418" cy="1098" r="3.5"/><circle cx="424" cy="1112" r="3.5"/><circle cx="430" cy="1102" r="3.5"/><circle cx="436" cy="1176" r="3.5"/><circle cx="442" cy="1168" r="3.5"/><circle cx="448" cy="1154" r="3.5"/><circle cx="454" cy="1186" r="3.5"/><circle cx="460" cy="1180" r="3.5"/><circle cx="468" cy="1198" r="3.5"/><circle cx="476" cy="1194" r="3.5"/><circle cx="484" cy="1190" r="3.5"/><circle cx="492" cy="1178" r="3.5"/><circle cx="496" cy="1152" r="3.5"/><circle cx="504" cy="1162" r="3.5"/><circle cx="512" cy="1142" r="3.5"/><circle cx="520" cy="1148" r="3.5"/><circle cx="526" cy="1140" r="3.5"/><circle cx="530" cy="1102" r="3.5"/><circle cx="536" cy="1092" r="3.5"/><circle cx="542" cy="1020" r="3.5"/><circle cx="550" cy="1018" r="3.5"/><circle cx="558" cy="1024" r="3.5"/><circle cx="568" cy="1028" r="3.5"/><circle cx="574" cy="1038" r="3.5"/>
      <circle cx="578" cy="1194" r="3.5"/><circle cx="590" cy="1190" r="3.5"/><circle cx="600" cy="1186" r="3.5"/><circle cx="610" cy="1182" r="3.5"/><circle cx="620" cy="1180" r="3.5"/><circle cx="630" cy="1188" r="3.5"/><circle cx="638" cy="1192" r="3.5"/><circle cx="644" cy="1170" r="3.5"/><circle cx="652" cy="1154" r="3.5"/><circle cx="656" cy="1082" r="3.5"/><circle cx="660" cy="1132" r="3.5"/><circle cx="668" cy="1080" r="3.5"/><circle cx="672" cy="1040" r="3.5"/><circle cx="682" cy="1036" r="3.5"/><circle cx="690" cy="1094" r="3.5"/><circle cx="696" cy="1162" r="3.5"/><circle cx="702" cy="1172" r="3.5"/><circle cx="706" cy="1046" r="3.5"/><circle cx="710" cy="1060" r="3.5"/><circle cx="716" cy="1074" r="3.5"/><circle cx="722" cy="1028" r="3.5"/><circle cx="722" cy="1118" r="3.5"/><circle cx="732" cy="1044" r="3.5"/><circle cx="740" cy="1034" r="3.5"/><circle cx="750" cy="1028" r="3.5"/>
    </g>
    <g fill="var(--blue)">
      <circle cx="205" cy="1028" r="3.5"/><circle cx="210" cy="1022" r="3.5"/><circle cx="218" cy="1026" r="3.5"/><circle cx="203" cy="1082" r="3.5"/>
      <circle cx="220" cy="1100" r="3.5"/><circle cx="226" cy="1132" r="3.5"/><circle cx="232" cy="1124" r="3.5"/><circle cx="236" cy="1146" r="3.5"/><circle cx="240" cy="1160" r="3.5"/><circle cx="246" cy="1136" r="3.5"/><circle cx="252" cy="1130" r="3.5"/><circle cx="256" cy="1096" r="3.5"/><circle cx="260" cy="1118" r="3.5"/><circle cx="266" cy="1122" r="3.5"/><circle cx="270" cy="1098" r="3.5"/><circle cx="276" cy="1158" r="3.5"/><circle cx="282" cy="1150" r="3.5"/><circle cx="286" cy="1120" r="3.5"/><circle cx="292" cy="1134" r="3.5"/><circle cx="298" cy="1162" r="3.5"/><circle cx="304" cy="1152" r="3.5"/><circle cx="310" cy="1146" r="3.5"/><circle cx="316" cy="1160" r="3.5"/><circle cx="322" cy="1154" r="3.5"/><circle cx="332" cy="1166" r="3.5"/><circle cx="338" cy="1186" r="3.5"/><circle cx="346" cy="1182" r="3.5"/><circle cx="352" cy="1178" r="3.5"/><circle cx="360" cy="1186" r="3.5"/><circle cx="368" cy="1174" r="3.5"/><circle cx="376" cy="1180" r="3.5"/><circle cx="382" cy="1162" r="3.5"/><circle cx="388" cy="1154" r="3.5"/><circle cx="394" cy="1148" r="3.5"/><circle cx="402" cy="1164" r="3.5"/><circle cx="410" cy="1170" r="3.5"/><circle cx="416" cy="1150" r="3.5"/><circle cx="422" cy="1168" r="3.5"/><circle cx="430" cy="1164" r="3.5"/><circle cx="436" cy="1200" r="3.5"/><circle cx="444" cy="1196" r="3.5"/><circle cx="450" cy="1172" r="3.5"/><circle cx="456" cy="1178" r="3.5"/><circle cx="460" cy="1148" r="3.5"/><circle cx="464" cy="1188" r="3.5"/><circle cx="464" cy="1074" r="3.5"/><circle cx="470" cy="1046" r="3.5"/><circle cx="476" cy="1040" r="3.5"/><circle cx="480" cy="1032" r="3.5"/><circle cx="484" cy="1056" r="3.5"/><circle cx="490" cy="1054" r="3.5"/><circle cx="496" cy="1184" r="3.5"/><circle cx="502" cy="1172" r="3.5"/><circle cx="508" cy="1158" r="3.5"/><circle cx="516" cy="1158" r="3.5"/><circle cx="526" cy="1168" r="3.5"/><circle cx="532" cy="1124" r="3.5"/><circle cx="540" cy="1124" r="3.5"/><circle cx="544" cy="1038" r="3.5"/><circle cx="552" cy="1028" r="3.5"/><circle cx="560" cy="1022" r="3.5"/><circle cx="572" cy="1030" r="3.5"/><circle cx="580" cy="1022" r="3.5"/>
    </g>
    <text x="1132" y="1020" font-family="serif" font-size="11" fill="#333">Names</text>
    <g>
      <circle cx="1114" cy="1016" r="3" fill="#9ab8dc"/><circle cx="1114" cy="1035" r="3" fill="#f0b27a"/><circle cx="1114" cy="1054" r="3" fill="var(--green)"/><circle cx="1114" cy="1073" r="3" fill="#d96b6b"/><circle cx="1114" cy="1091" r="3" fill="#b99ad9"/><circle cx="1114" cy="1110" r="3" fill="#b08c82"/><circle cx="1114" cy="1128" r="3" fill="#e5a6cf"/><circle cx="1114" cy="1147" r="3" fill="#aaaaaa"/><circle cx="1114" cy="1165" r="3" fill="var(--olive)"/><circle cx="1114" cy="1184" r="3" fill="#8fd3e0"/><circle cx="1114" cy="1203" r="3" fill="var(--blue)"/>
    </g>
  </svg>
</section>
</body>
</html>
```